Presentation for new businessconcept from mediacompany

We have a need of an presentation for our bussinessidea within media.

Attatched is the presentation in text, we need illustrations that shows what we can do in same graphic theme as our logo and site: www.lumiferra.com

As little text as possible since we will use this for presentations but u should still be able to understand every slide without hearing the words.

Please PM me for more info, possible movieproject for same issue will be relevant in beginning of next year as well.

The PelkinTot-bee is right now attatched on the logo so feel free to play with him, just as long we can tell he is the one there :)
Updates

Forget to say, the presentation is going to be in swedish so we will change all the text, please use images only according to the description.

Target Market(s)

People who work with marketing and communication i all kinds of companies.

Industry/Entity Type

Media

Requirements
Must have
• The files we upload is the logo and a rough example of situations we like our pelkintot-bee to be in in the presentation. you are free to come with other suggestions, this is only to give you a hint of what we are looking for.
Please use same colors as we have on www.lumiferra.com
Nice to have
• We would really love it if our Lumiferra Bee were to be an important part in all the slides, like showing, pointing, acting etc in different forms.
Should not have
• We dont want photos or real people, we like it more like a cartoon with our Lumiferra bee as a maincharrachter.

```html
<!DOCTYPE html>
<html lang="en">
<head>
<meta charset="utf-8">
<title>Lumiferra – Business Presentation</title>
<link rel="stylesheet" href="https://fonts.googleapis.com/css2?family=Delius&family=Varela+Round&display=swap">
<style>
  :root {
    --leaf: #a8b800;
    --leaf-dark: #5a6a10;
    --lemon: #f4f400;
    --cream: #fffff0;
    --cream-deep: #f8f8c4;
    --paper: #efefef;
    --ink: #6f6f6f;
    --ink-dark: #333333;
    --orange: #f0a000;
    --white: #ffffff;
  }
  * { box-sizing: border-box; margin: 0; padding: 0; }
  html, body { width: 1200px; height: 656px; overflow: hidden; background: var(--white); }
  .canvas { position: relative; width: 1200px; height: 656px; background: var(--white); overflow: hidden; }

  .slide { position: absolute; width: 469px; height: 256px; overflow: hidden; background: var(--paper); }
  .slide--welcome { left: 106px; top: 81px; background: var(--leaf); }
  .slide--idea { left: 575px; top: 81px; }
  .slide--heroes { left: 106px; top: 337px; }
  .slide--targeted { left: 575px; top: 337px; }

  .slide__curve { position: absolute; inset: 0; width: 469px; height: 256px; }

  .heading { position: absolute; font-family: "Delius", "Comic Sans MS", cursive; color: var(--leaf); font-size: 16px; line-height: 1; white-space: nowrap; }
  .heading__accent { color: var(--orange); }
  .heading__rule { position: absolute; }
  .heading__dot { position: absolute; width: 9px; height: 9px; border-radius: 50%; background: var(--leaf-dark); }

  .brand { position: absolute; font-family: "Varela Round", Arial, sans-serif; font-weight: 400; color: var(--leaf-dark); white-space: nowrap; display: flex; align-items: center; gap: 3px; }
  .brand__dot { width: 6px; height: 6px; border-radius: 50%; background: var(--leaf); }
  .brand--large { font-size: 15px; }
  .brand--small { font-size: 9px; }

  .body-text { position: absolute; font-family: "Varela Round", Arial, sans-serif; color: var(--ink); }
  .body-text strong { color: var(--ink-dark); }
  .body-text .name-accent { color: var(--leaf); }

  .art { position: absolute; border-radius: 40% 40% 30% 30%; }

  /* Welcome */
  .welcome-title { position: absolute; left: 161px; top: 106px; font-family: "Delius", cursive; color: var(--white); font-size: 17px; white-space: nowrap; }
  .welcome-title small { font-size: 7px; }
  .welcome-title .welcome-title__accent { color: var(--lemon); font-size: 11px; }

  /* Idea */
  .idea-text { left: 93px; top: 106px; width: 250px; font-size: 12.5px; line-height: 17px; font-weight: 700; }

  /* Heroes */
  .heroes-lead { left: 94px; top: 82px; width: 250px; font-size: 10px; line-height: 14px; font-weight: 700; }
  .hero-list { position: absolute; left: 118px; top: 138px; list-style: none; font-family: "Varela Round", Arial, sans-serif; font-size: 7.5px; color: var(--leaf); }
  .hero-list li { display: flex; align-items: center; gap: 6px; height: 15px; }
  .hero-list li::before { content: ""; width: 6px; height: 6px; border-radius: 50%; background: var(--leaf-dark); }
  .heroes-close { left: 94px; top: 174px; font-size: 10px; font-weight: 700; }

  /* Targeted */
  .targeted-text { left: 95px; top: 72px; width: 250px; font-size: 7px; line-height: 10px; }
  .targeted-text p { margin-bottom: 9px; }
  .targeted-text .link { color: var(--leaf); }
</style>
</head>
<body>
<main class="canvas">

  <!-- Slide 1: Welcome -->
  <section class="slide slide--welcome">
    <svg class="slide__curve" viewBox="0 0 469 256" aria-hidden="true">
      <defs>
        <linearGradient id="welcomeGlow" x1="0" y1="0" x2="1" y2="1">
          <stop offset="0" stop-color="#fffff6"/>
          <stop offset="1" stop-color="#f6f6b8"/>
        </linearGradient>
      </defs>
      <path d="M469 0 C420 30 350 120 372 185 C388 228 430 248 469 256 Z" fill="url(#welcomeGlow)"/>
      <path d="M148 130 L335 130 Q343 130 346 136" fill="none" stroke="#3d4a0a" stroke-width="1.5"/>
    </svg>
    <span class="heading__dot" style="left:135px; top:117px;"></span>
    <h1 class="welcome-title">Welcome <small>to this</small> <span class="welcome-title__accent">Presentation</span></h1>
    <div class="brand brand--large" style="left:370px; top:150px;"><span class="brand__dot"></span>Lumiferra</div>
  </section>

  <!-- Slide 2: Business idea -->
  <section class="slide slide--idea">
    <svg class="slide__curve" viewBox="0 0 469 256" aria-hidden="true">
      <path d="M469 10 C410 50 335 110 350 170 C362 215 420 245 469 256 Z" fill="var(--white)"/>
      <path d="M110 43 L398 43 Q405 43 408 50" fill="none" stroke="var(--leaf-dark)" stroke-width="1.2"/>
    </svg>
    <span class="heading__dot" style="left:94px; top:32px;"></span>
    <h2 class="heading" style="left:122px; top:23px;">Our Businessidea</h2>
    <p class="body-text idea-text"><strong>Lumiferra</strong> will offer systems that, through cross-marketing, meet defined target in a cost effective manner.</p>
    <div class="art" role="img" aria-label="Cartoon presenter pointing with a stick" style="left:362px; top:105px; width:95px; height:80px; background:linear-gradient(160deg,#f1d9b5,#2f5fb0 60%,#6b3b1a);"></div>
    <div class="brand brand--small" style="left:372px; top:234px;"><span class="brand__dot"></span>Lumiferra</div>
  </section>

  <!-- Slide 3: Heroes -->
  <section class="slide slide--heroes">
    <svg class="slide__curve" viewBox="0 0 469 256" aria-hidden="true">
      <path d="M469 0 C400 40 330 110 348 170 C362 215 420 245 469 256 Z" fill="var(--white)"/>
      <path d="M108 43 L398 43 Q405 43 408 50" fill="none" stroke="var(--leaf-dark)" stroke-width="1.2"/>
    </svg>
    <span class="heading__dot" style="left:95px; top:32px;"></span>
    <h2 class="heading" style="left:122px; top:23px;">We create heroes!</h2>
    <p class="body-text heroes-lead">By <strong>Lumi<span class="name-accent">ferra</span></strong> system of " PelkinTots " the customer is offered guaranteed exposures , which makes a PelkinTot for a hero by :</p>
    <ul class="hero-list">
      <li>Charity</li>
      <li>Incentives - back to that which divides</li>
    </ul>
    <p class="body-text heroes-close">This focus on increasing loyalty and brand recognition.</p>
    <div class="art" role="img" aria-label="Cartoon superhero flying with a red and yellow cape" style="left:350px; top:78px; width:118px; height:92px; background:linear-gradient(200deg,#d84030,#f2e030 45%,#3070c8);"></div>
    <div class="brand brand--small" style="left:372px; top:234px;"><span class="brand__dot"></span>Lumiferra</div>
  </section>

  <!-- Slide 4: Targeted -->
  <section class="slide slide--targeted">
    <svg class="slide__curve" viewBox="0 0 469 256" aria-hidden="true">
      <path d="M469 0 C400 40 330 110 348 170 C362 215 420 245 469 256 Z" fill="var(--white)"/>
      <path d="M110 43 L398 43 Q405 43 408 50" fill="none" stroke="var(--leaf-dark)" stroke-width="1.2"/>
    </svg>
    <span class="heading__dot" style="left:94px; top:32px;"></span>
    <h2 class="heading" style="left:119px; top:23px;">Targeted and <span class="heading__accent">cost-effective</span></h2>
    <div class="body-text targeted-text">
      <p>By cooperation with already known partners will campaign cost-effective and can reach a larger audience.</p>
      <p>Importantly, however, we are working towards is already pre-defined target groups in order to reduce the risk of "waste".</p>
      <p>Ex . on collaborations that work :<br>Norvik Foods - <span class="link">http://www.clipvault.net/watch?v=k7rPqLm2</span></p>
      <p>All is not Norvik Foods and the target audience is rarely the whole Swedish people. Therefore, we want to offer the same thing that Norvik Foods does, but with focusing on your target audience and possible. budget.</p>
    </div>
    <div class="art" role="img" aria-label="Figure throwing a dart at a red target" style="left:385px; top:63px; width:85px; height:60px; background:linear-gradient(90deg,#d8d8d8,#ffffff 50%,#d02020);"></div>
    <div class="art" role="img" aria-label="Cartoon businessman counting money beside a stack of papers" style="left:378px; top:138px; width:88px; height:62px; background:linear-gradient(90deg,#e8e8e8,#2a2a2a 50%,#f4f4f4);"></div>
    <div class="brand brand--small" style="left:374px; top:234px;"><span class="brand__dot"></span>Lumiferra</div>
  </section>

</main>
</body>
</html>
```